KESTREL Academy Exhibit Booth Posters

My company is KESTREL Academy (a division of KESTREL for Growth). We are exhibiting in a month, and I need to re-do my exhibit booth posters. There will be a total of 4 posters needed. Sizes are below.
1) Top- 11 feet long X 12 inches wide (Try to match color scheme in example photo)
2) Center- 4 feet long X 2 feet wide (Chalkboard background)
3) Left- 18 inches long X 2 feet wide (Cork-board back ground with the use of push pins holding up post-it-notes, paper, etc.)
4) Right- 18 inches long X 2 feet wide (Cork-board back ground with the use of push pins holding up post-it-notes, paper, etc.)
I have attached a photo of my old booth. This will get you an idea of the size, color schemes, and more. I have created basic rendering of each poster. The content is important, but the look and design should be drastically improved.
The websites to look into for ideas are:
www.kestrelforgrowth.example
www.kestrelacademy.example
Updates
I've added a new file. It's a .JPG of the certification diploma. Thanks!
Target Market(s)
Business Owners, Managers, HR, Supervisors, Teens who want to boost their resume
Industry/Entity Type
It Company
Look and feel

```html
<!DOCTYPE html>
<html lang="en">
<head>
<meta charset="utf-8">
<title>KESTREL Academy – Get Your Employees Certified</title>
<link rel="stylesheet" href="https://fonts.googleapis.com/css2?family=Fredoka:wght@600&family=UnifrakturCook:wght@700&family=Crimson+Text:wght@400;600&family=Comic+Neue:wght@700&family=Kalam:wght@700&display=swap">
<style>
  :root {
    --wood-light: #d9a15a;
    --wood-dark: #a8672a;
    --cork: #c59a62;
    --cork-dark: #b0854f;
    --ribbon-light: #efe2c4;
    --ribbon-dark: #c9b48a;
    --heading-red: #d42a22;
    --ink-dark: #2a2a2a;
    --gold: #c9a03a;
    --gold-text: #b8892a;
    --paper: #fdfcf8;
    --tape: rgba(225, 228, 232, 0.72);
    --photo-bg: #8d9db0;
    --photo-shirt: #1f2a55;
    --banner-bg: #b9c4cf;
    --white: #ffffff;
  }
  * { box-sizing: border-box; margin: 0; padding: 0; }
  html, body { width: 900px; height: 1200px; overflow: hidden; background: var(--white); }

  .poster {
    position: relative;
    width: 900px; height: 1200px;
    background: linear-gradient(135deg, var(--wood-light), var(--wood-dark) 50%, var(--wood-light));
    overflow: hidden;
  }
  .cork {
    position: absolute; left: 42px; top: 38px; right: 42px; bottom: 40px;
    background: radial-gradient(circle at 40% 35%, var(--cork), var(--cork-dark));
    box-shadow: inset 0 0 14px rgba(0,0,0,0.45);
  }

  .headline {
    position: absolute; top: 48px; left: 0; width: 100%;
    text-align: center;
    font-family: "Fredoka", sans-serif; font-weight: 600; font-size: 50px;
    color: var(--white);
    -webkit-text-stroke: 2px #3a2a1a;
    paint-order: stroke fill;
    letter-spacing: 1px;
  }

  .ribbon { position: absolute; left: 40px; top: 118px; width: 800px; height: 180px; }
  .ribbon-title {
    position: absolute; top: 118px; left: 0; width: 100%;
    text-align: center;
    font-family: "UnifrakturCook", serif; font-weight: 700; font-size: 86px;
    color: var(--heading-red);
    text-shadow: 2px 3px 0 #5a1a12;
  }

  .certificate {
    position: absolute; left: 122px; top: 392px;
    width: 640px; height: 430px;
    transform: rotate(19deg); transform-origin: top left;
    background: var(--paper);
    padding: 14px;
    box-shadow: 4px 6px 10px rgba(0,0,0,0.35);
  }
  .certificate-border {
    width: 100%; height: 100%;
    border: 3px double var(--gold);
    outline: 8px solid rgba(201,160,58,0.35); outline-offset: -14px;
    text-align: center;
    padding-top: 108px;
    position: relative;
  }
  .certificate-title {
    font-family: "UnifrakturCook", serif; font-size: 44px; color: #555;
  }
  .certificate-lead {
    font-family: "Crimson Text", serif; font-size: 15px; letter-spacing: 3px;
    color: var(--gold-text); text-transform: uppercase; line-height: 1.1; margin-top: 8px;
  }
  .certificate-name {
    font-family: "Crimson Text", serif; font-size: 22px; color: var(--ink-dark);
    display: inline-block; border-bottom: 1px solid var(--gold);
    padding: 6px 50px 2px; margin-top: 4px;
  }
  .certificate-date {
    font-family: "Crimson Text", serif; font-size: 14px; letter-spacing: 3px;
    color: var(--gold-text); text-transform: uppercase; margin-top: 10px;
  }
  .signature {
    position: absolute; bottom: 72px; width: 150px;
    font-family: "Crimson Text", serif; font-size: 9px; letter-spacing: 1px;
    color: #777; text-transform: uppercase; text-align: left;
  }
  .signature-mark { height: 16px; border-bottom: 1px solid #999; margin-bottom: 3px; background: linear-gradient(transparent 60%, rgba(60,60,60,0.15)); }
  .signature.president { left: 24px; }
  .signature.vice { right: 24px; }
  .academy-mark {
    position: absolute; bottom: 60px; left: 50%; transform: translateX(-50%);
    display: flex; align-items: center; gap: 6px;
    font-family: "Crimson Text", serif; font-weight: 600; font-size: 17px; color: var(--heading-red);
    white-space: nowrap;
  }
  .academy-mark-dot { width: 14px; height: 14px; border-radius: 50%; background: #2a4fa0; }

  .snapshot {
    position: absolute; width: 212px; height: 290px;
    background: var(--white); padding: 6px;
    box-shadow: 3px 5px 9px rgba(0,0,0,0.4);
  }
  .snapshot-photo {
    width: 100%; height: 100%;
    background: linear-gradient(180deg, var(--photo-bg) 0%, var(--photo-bg) 45%, var(--photo-shirt) 45%, var(--photo-shirt) 100%);
  }
  .snapshot-label {
    position: absolute; top: 22px; right: 18px;
    font-family: "Kalam", cursive; font-weight: 700; font-size: 19px; color: var(--white);
  }
  .snapshot.before { left: 608px; top: 346px; transform: rotate(8deg); }
  .snapshot.after { left: 582px; top: 700px; transform: rotate(-8deg); }

  .tape { position: absolute; width: 90px; height: 32px; background: var(--tape); box-shadow: 0 1px 2px rgba(0,0,0,0.15); }

  .price-banner {
    position: absolute; left: 75px; top: 1006px; width: 746px; height: 150px;
  }
  .price-text {
    position: absolute; top: 1030px; left: 75px; width: 746px; text-align: center;
    font-family: "Comic Neue", sans-serif; font-weight: 700; font-size: 46px;
    color: var(--heading-red);
  }
</style>
</head>
<body>
<main class="poster">
  <div class="cork"></div>

  <h1 class="headline">Get Your Employees</h1>

  <svg class="ribbon" viewBox="0 0 800 180" aria-hidden="true">
    <defs>
      <linearGradient id="ribbonShade" x1="0" y1="0" x2="0" y2="1">
        <stop offset="0" stop-color="var(--ribbon-light)"/>
        <stop offset="1" stop-color="var(--ribbon-dark)"/>
      </linearGradient>
    </defs>
    <path d="M0 70 L150 60 L150 150 L30 165 Z" fill="var(--ribbon-dark)"/>
    <path d="M800 100 L650 60 L650 150 L760 175 Z" fill="var(--ribbon-dark)"/>
    <path d="M120 40 Q400 -10 680 40 L680 125 Q400 80 120 125 Z" fill="url(#ribbonShade)"/>
  </svg>
  <h2 class="ribbon-title">Certified</h2>

  <section class="certificate" aria-label="Sample certificate of achievement">
    <div class="certificate-border">
      <h3 class="certificate-title">Certificate of Achievement</h3>
      <p class="certificate-lead">This certificate is proudly<br>presented for honorable achievement to</p>
      <p class="certificate-name">Evan R. Marlowe</p>
      <p class="certificate-date">Awarded this day of June 21st, 2010</p>
      <div class="signature president"><div class="signature-mark"></div>Owen T. Hale, President</div>
      <div class="academy-mark"><span class="academy-mark-dot"></span>KESTREL Academy</div>
      <div class="signature vice"><div class="signature-mark"></div>Mara K. Lynd, Vice-President</div>
    </div>
  </section>

  <figure class="snapshot before">
    <div class="snapshot-photo" role="img" aria-label="Photo of an employee before certification, casually styled in a navy polo"></div>
    <span class="snapshot-label">Before</span>
  </figure>
  <figure class="snapshot after">
    <div class="snapshot-photo" role="img" aria-label="Photo of the same employee after certification, neatly groomed in a navy polo with ID badge"></div>
    <span class="snapshot-label">After</span>
  </figure>

  <div class="tape" style="left:640px;top:330px;transform:rotate(-20deg)"></div>
  <div class="tape" style="left:745px;top:600px;transform:rotate(-35deg)"></div>
  <div class="tape" style="left:605px;top:700px;transform:rotate(25deg)"></div>
  <div class="tape" style="left:740px;top:895px;transform:rotate(-45deg)"></div>

  <svg class="price-banner" viewBox="0 0 746 150" aria-hidden="true">
    <rect x="0" y="0" width="746" height="150" fill="var(--banner-bg)"/>
    <path d="M0 118 L30 124 L55 112 L90 126 L120 116 L160 128 L200 114 L240 124 L280 112 L320 126 L360 118 L400 128 L440 114 L480 124 L520 112 L560 126 L600 116 L640 128 L680 114 L720 122 L746 116 L746 150 L0 150 Z" fill="var(--white)"/>
  </svg>
  <p class="price-text">At a Price You cannot Pass Up!</p>
</main>
</body>
</html>
```